Business Intelligence Dashboard header

We are a top 10 cancer treatment clinic. Our analytics teams (Corporate Finance, Financial Analytics, and Clinical Analytics) are searching for a great graphic to show our business partners the value of our business intelligence products. We are hoping to convey that we are tech-savvy, supportive to our patients and mission of saving lives, valuable, forward-thinking, agile, supportive, and friendly.

This header will be placed at the top of each data visualization ('viz') that we create. We would like a design that is in-line with our company branding, simple, elegant, and striking. We primarily create headers that are between 800 and 1300 pixels across (800 and 1300 being the most common) and between 60 and 80 pixels high (76 being our current header height in px, but we are open to slight deviation.) The type of data visualizations this will sit atop (everything we produce, but just a few examples) will be things like patient safety, clinic utilization, appointment volumes, provider scorecards, and many more. I've included our current header, and a header I saw and liked (although I think it could have been a bit cooler.)

I'm open to ideas, feedback, and your opinion as a designer to come up with something amazing. You can find our website at https://www.harbornorthclinic.org/
Searching our business shows our main clinic (with the rounded front) https://www.findexo.com/search?q=harbor+north+oncology+partners&source=lnms&tbm=isch&sa=X&ved=0ahUKEwjjws22xuLXAhVM5mMKHb82CpQQ_AUIDCgD&biw=1995&bih=916

We are open to stock images.

Industry/Entity Type

Business

Requirements
Must have
• A place to write in a dashboard title (we will use our own BI-native object to float over the top of this banner)
Nice to have
• We would like a place/icon to differentiate between work products coming out of Clinical Analytics/Financial Analytics/Corporate Finance. We're fine with it being on 2 lines, or simply designing an icon to differentiate. We could use smaller text underneath the dashboard title (see must haves), an icon for each of the 3 teams, or a space in the header to write in the team ourselves. The team names should be of limited significance on the header. The star of the show will be the dashboard title (just leave an area for it) where the team names should be of less significance (off to the side, under the title in smaller font, etc)

```html
<!DOCTYPE html>
<html lang="en">
<head>
<meta charset="utf-8">
<title>Dashboard Headers</title>
<link href="https://fonts.googleapis.com/css2?family=Open+Sans:wght@400;600;700&display=swap" rel="stylesheet">
<style>
  :root{
    --bg:#121212;
    --slate:#6e6663;
    --sun:#ffc61e;
    --sun-edge:#f3a21a;
    --amber:#a6560d;
    --title:#7a4700;
    --white:#ffffff;
  }
  *{margin:0;padding:0;box-sizing:border-box}
  html,body{width:1200px;height:573px;overflow:hidden;background:var(--bg);font-family:"Open Sans",Arial,sans-serif}
  .board{position:relative;width:1200px;height:573px}
  .header-bar{position:absolute;left:80px;width:1040px;height:64px;overflow:hidden}
  .header-bar.clinical{top:110px}
  .header-bar.corporate{top:255px}
  .header-bar.financial{top:401px}
  .bar-shape{position:absolute;inset:0}
  .theme-image{position:absolute;left:460px;top:0;width:580px;height:64px;
    background:linear-gradient(90deg,rgba(255,198,30,0) 0%,rgba(240,176,30,.85) 22%,#e4a01c 45%,#cd8015 75%,var(--amber) 100%)}
  .brand{position:absolute;left:21px;top:10px;display:flex;align-items:flex-start;gap:4px}
  .brand-name{color:var(--white);font-weight:700;font-size:11px;line-height:13px;letter-spacing:-.2px}
  .brand-dot{width:14px;height:14px;border-radius:50%;background:var(--sun);margin-top:-2px}
  .dashboard-title{position:absolute;left:175px;top:0;height:64px;line-height:64px;font-size:29px;font-weight:600;color:var(--title);letter-spacing:-.2px;white-space:nowrap}
  .team{position:absolute;left:926px;top:0;height:64px;display:flex;align-items:center;gap:9px}
  .team-icon{width:28px;height:28px;border-radius:50%;background:var(--sun);display:flex;align-items:center;justify-content:center}
  .team-name{color:var(--white);font-size:14px;line-height:14.5px;font-weight:400}
</style>
</head>
<body>
<div class="board">

  <section class="header-bar clinical">
    <svg class="bar-shape" width="1040" height="64" viewBox="0 0 1040 64" aria-hidden="true">
      <rect width="200" height="64" fill="var(--slate)"/>
      <path d="M116 0 H200 V64 H160 C128 64 117 40 116 0Z" fill="var(--sun-edge)"/>
      <path d="M121 0 H1040 V64 H172 C136 64 122 40 121 0Z" fill="var(--sun)"/>
    </svg>
    <div class="theme-image" role="img" aria-label="Golden-toned photo of the main clinic building with its rounded front under a cloudy sky"></div>
    <div class="brand"><span class="brand-name">Harbor North<br>Oncology<br>Partners</span><span class="brand-dot"></span></div>
    <h1 class="dashboard-title">Your Dashboard Title</h1>
    <div class="team">
      <span class="team-icon"><svg width="20" height="14" viewBox="0 0 20 14"><polyline points="0,7 5,7 7,3 9,12 11,1 13,9 14,7 20,7" fill="none" stroke="var(--amber)" stroke-width="1.8" stroke-linejoin="round"/></svg></span>
      <span class="team-name">Clinical<br>Analytics</span>
    </div>
  </section>

  <section class="header-bar corporate">
    <svg class="bar-shape" width="1040" height="64" viewBox="0 0 1040 64" aria-hidden="true">
      <rect width="200" height="64" fill="var(--slate)"/>
      <path d="M116 0 H200 V64 H160 C128 64 117 40 116 0Z" fill="var(--sun-edge)"/>
      <path d="M121 0 H1040 V64 H172 C136 64 122 40 121 0Z" fill="var(--sun)"/>
    </svg>
    <div class="theme-image" role="img" aria-label="Golden-toned illustration of coins and interlocking gears"></div>
    <div class="brand"><span class="brand-name">Harbor North<br>Oncology<br>Partners</span><span class="brand-dot"></span></div>
    <h1 class="dashboard-title">Your Dashboard Title</h1>
    <div class="team">
      <span class="team-icon"><svg width="16" height="16" viewBox="0 0 16 16"><rect x="1" y="7" width="3.5" height="9" fill="var(--amber)"/><rect x="6.2" y="2" width="3.5" height="14" fill="var(--amber)"/><rect x="11.4" y="9" width="3.5" height="7" fill="var(--amber)"/></svg></span>
      <span class="team-name">Corporate<br>Finance</span>
    </div>
  </section>

  <section class="header-bar financial">
    <svg class="bar-shape" width="1040" height="64" viewBox="0 0 1040 64" aria-hidden="true">
      <rect width="200" height="64" fill="var(--slate)"/>
      <path d="M116 0 H200 V64 H160 C128 64 117 40 116 0Z" fill="var(--sun-edge)"/>
      <path d="M121 0 H1040 V64 H172 C136 64 122 40 121 0Z" fill="var(--sun)"/>
    </svg>
    <div class="theme-image" role="img" aria-label="Golden-toned illustration of a business person facing sketched charts and finance doodles"></div>
    <div class="brand"><span class="brand-name">Harbor North<br>Oncology<br>Partners</span><span class="brand-dot"></span></div>
    <h1 class="dashboard-title">Your Dashboard Title</h1>
    <div class="team">
      <span class="team-icon"><svg width="18" height="14" viewBox="0 0 18 14"><polyline points="1,12 6,5 10,9 17,2" fill="none" stroke="var(--amber)" stroke-width="2.4" stroke-linecap="round" stroke-linejoin="round"/></svg></span>
      <span class="team-name">Financial<br>Analytics</span>
    </div>
  </section>

</div>
</body>
</html>
```